KRT Engineering Business Card Design

We’re looking for an elegant, clean, and timeless business card design that communicates experience, capability, and reliability.

KRT Engineering was established in 1995 , we are a Government Contracting company providing Professional Services to the Office of Frontier Affairs, Harbor Protection and the Vantage Collective. Our capabilities include: Acquisition & Program Management; Intelligence & Security Operations; Cyber, IT & Network Operations; Lifecycle Logistics & Asset Readiness; C5ISR Systems Engineering & Sustainment.

We want the card to reflect a straightforward, confident approach to business. The design should feel polished and professional without being flashy or overly corporate.

Design Direction
Clean, sophisticated, and uncluttered
Elegant but understated
Strong typography and thoughtful spacing
A timeless aesthetic rather than something overly trendy
Confident and established, with a sense of substance
Easy to read and practical in a real-world business setting

The overall impression should be: “These are experienced professionals who know what they’re doing, do what they say, and can be relied upon.”

We’re open to creative interpretations. The finished card should feel distinctive through its typography, proportions, layout, and attention to detail rather than through excessive graphics or visual effects.

We’re looking for a design that would make a potential client immediately feel that they’re dealing with a capable, trustworthy, and established company.

Company Colors: Navy and Gold/Yellow (but you do not need to use these colors on the card)
Company Name: KRT Engineering Associates, Inc. (known as KRT Engineering)
Website: krtengineering.com
Company Logo: Navy & Gold (other variations attached)

```html
<!DOCTYPE html>
<html lang="en">
<head>
<meta charset="utf-8">
<title>KRT Engineering Business Card</title>
<link rel="stylesheet" href="https://fonts.googleapis.com/css2?family=Montserrat:wght@400;700&family=Lato:wght@400&display=swap">
<style>
  :root {
    --navy: #212b5e;
    --navy-deep: #1c2652;
    --gold: #fbe04a;
    --white: #ffffff;
    --ink: #1a1a1a;
    --ink-soft: #3a3a3a;
    --backdrop: #9a9a9a;
  }
  * { margin: 0; padding: 0; box-sizing: border-box; }
  html, body {
    width: 1200px; height: 1059px; overflow: hidden;
    background: var(--backdrop);
  }
  .canvas { position: relative; width: 1200px; height: 1059px; }

  .card {
    position: absolute;
    border-radius: 29px;
    overflow: hidden;
  }
  .card--front { left: 258px; top: 83px; width: 704px; height: 402px; background: var(--white); }
  .card--back { left: 254px; top: 561px; width: 714px; height: 407px; background: var(--navy); }

  .wordmark {
    position: absolute;
    font-family: "Montserrat", sans-serif;
    font-weight: 700;
    white-space: nowrap;
    letter-spacing: 0.5px;
    transform: translate(-50%, -50%);
  }
  .card--front .wordmark { left: 189px; top: 200px; font-size: 34px; color: var(--navy); }
  .card--back .wordmark { left: 357px; top: 200px; font-size: 46px; color: var(--white); }

  .divider {
    position: absolute; left: 375px; top: 93px;
    width: 2px; height: 214px;
    background: linear-gradient(to bottom, transparent, var(--navy) 12%, var(--navy) 88%, transparent);
  }

  .identity { position: absolute; left: 409px; top: 90px; }
  .identity__name {
    font-family: "Montserrat", sans-serif; font-weight: 700;
    font-size: 26px; color: var(--navy); letter-spacing: 0.6px; line-height: 1;
  }
  .identity__role {
    margin-top: 8px;
    font-family: "Montserrat", sans-serif; font-weight: 400;
    font-size: 18.5px; color: var(--ink-soft); letter-spacing: 0.5px; line-height: 1;
  }

  .contacts { position: absolute; left: 409px; top: 163px; list-style: none; }
  .contacts__item {
    display: flex; align-items: center; height: 29px;
    font-family: "Lato", sans-serif; font-size: 19px; color: var(--ink);
  }
  .contacts__item--web { color: var(--ink-soft); }
  .contacts__icon { width: 24px; height: 20px; margin-right: 14px; flex: none; }

  .address {
    position: absolute; left: 413px; top: 262px;
    font-family: "Lato", sans-serif; font-size: 19px; line-height: 23px;
    color: var(--ink); font-style: normal;
  }

  .base-band { position: absolute; left: 0; bottom: 0; width: 100%; height: 16px; }
</style>
</head>
<body>
<main class="canvas">

  <section class="card card--front" aria-label="Business card front">
    <div class="wordmark">KRT Engineering</div>
    <div class="divider"></div>

    <div class="identity">
      <p class="identity__name">DANIEL MORROW</p>
      <p class="identity__role">MANAGING DIRECTOR</p>
    </div>

    <ul class="contacts">
      <li class="contacts__item">
        <svg class="contacts__icon" viewBox="0 0 24 24" aria-hidden="true">
          <path fill="var(--navy)" d="M6.6 3.5l3 3.4-1.9 2.2c1.2 2.5 3 4.4 5.4 5.6l2.2-1.9 3.4 3-1.8 3c-7.2-.5-12.6-5.9-13.3-13.1z"/>
          <path fill="none" stroke="var(--gold)" stroke-width="1.6" d="M14 3.5a6.5 6.5 0 0 1 6.5 6.5M14 6.8a3.2 3.2 0 0 1 3.2 3.2"/>
        </svg>
        044-555 210 347
      </li>
      <li class="contacts__item">
        <svg class="contacts__icon" viewBox="0 0 24 20" aria-hidden="true">
          <rect x="1" y="3" width="22" height="15" fill="var(--navy)"/>
          <path d="M1 3l11 8 11-8" fill="none" stroke="var(--white)" stroke-width="1.8"/>
        </svg>
        info@krtengineering.com
      </li>
      <li class="contacts__item contacts__item--web">
        <svg class="contacts__icon" viewBox="0 0 24 24" aria-hidden="true">
          <circle cx="12" cy="12" r="9.5" fill="none" stroke="var(--navy)" stroke-width="2"/>
          <path fill="var(--navy)" d="M7 6.5c2 .5 3 2 2.5 3.5s-2 1.5-2 3 1.5 2 1 4c-2-1-3.5-3.5-3.5-5.5 0-2 .8-3.7 2-5zM14 9c1.5 0 3 1 3.5 2.5s-1 3-2 4.5-2 2.5-2.5 1c0-1.5-1.5-2-1-3.5S12.5 9 14 9z"/>
        </svg>
        krtengineering.com
      </li>
    </ul>

    <address class="address">421, Address line goes here<br>45452, Country name</address>

    <svg class="base-band" viewBox="0 0 704 16" preserveAspectRatio="none" aria-hidden="true">
      <polygon points="0,0 360,0 335,16 0,16" fill="var(--navy)"/>
      <polygon points="370,0 704,0 704,16 345,16" fill="var(--gold)"/>
    </svg>
  </section>

  <section class="card card--back" aria-label="Business card back">
    <div class="wordmark">KRT Engineering</div>
    <svg class="base-band" viewBox="0 0 714 16" preserveAspectRatio="none" aria-hidden="true">
      <polygon points="0,0 372,0 342,16 0,16" fill="var(--navy-deep)"/>
      <polygon points="380,0 714,0 714,16 350,16" fill="var(--navy-deep)"/>
    </svg>
  </section>

</main>
</body>
</html>
```